Q + Public Adjusters Collective Business card

We need to get business card Design for our Company we are Public Adjusters in Chicago Illinois - i like to see good combination and elements from my Company Logo. as well To be an two side design
Updates

Target Market(s)

Home /Business owner Property Managers

Industry/Entity Type

Business

Contact Information for Business Card

to show the Element of our logo i will Like 3D

Font styles to use
Sans Serif

Requirements
Must have
• Logo and Element of the Logo in 3D
Nice to have
• Logo That we Provide 3D Same Colors or open for suggestions
Should not have
• unleare view -

```html
<!DOCTYPE html>
<html lang="en">
<head>
<meta charset="utf-8">
<title>Public Adjusters Collective – Business Card</title>
<link rel="stylesheet" href="https://fonts.googleapis.com/css2?family=Open+Sans:wght@400;600;800&display=swap">
<style>
  :root {
    --navy: #0d1a8c;
    --orange: #e0593a;
    --ink: #4a4a4a;
    --card: #ffffff;
    --stage: #eceef1;
  }
  * { margin: 0; padding: 0; box-sizing: border-box; }
  html, body { width: 1200px; height: 900px; overflow: hidden; }
  body {
    background: var(--stage);
    font-family: "Open Sans", Arial, sans-serif;
    position: relative;
  }
  .card {
    position: absolute;
    left: 280px;
    width: 640px;
    height: 366px;
    background: var(--card);
    box-shadow: 0 2px 10px rgba(0,0,0,0.12);
    overflow: hidden;
  }
  .card--front { top: 70px; }
  .card--back { top: 464px; }

  /* front side */
  .front-brand {
    position: absolute;
    inset: 0;
    display: flex;
    flex-direction: column;
    align-items: center;
    justify-content: center;
    gap: 24px;
  }
  .brand-dot {
    width: 110px; height: 110px;
    border-radius: 50%;
    background: var(--navy);
  }
  .brand-name {
    font-weight: 800;
    font-size: 30px;
    color: var(--navy);
    white-space: nowrap;
  }

  /* back side */
  .back-art { position: absolute; inset: 0; }
  .person { position: absolute; left: 68px; top: 28px; }
  .person-name { color: var(--orange); font-size: 20px; font-weight: 600; line-height: 1.1; }
  .person-role { color: var(--ink); font-size: 13px; line-height: 1.3; }
  .contact {
    position: absolute; left: 40px; top: 166px;
    color: var(--ink); font-size: 15px; line-height: 1.45;
    list-style: none;
  }
  .contact li { display: flex; align-items: center; gap: 10px; }
  .contact .address { padding-left: 20px; }
  .contact svg { width: 10px; height: 10px; flex: none; }
  .back-brand {
    position: absolute; left: 380px; top: 70px; width: 230px;
    display: flex; flex-direction: column; align-items: center; gap: 14px;
  }
  .back-brand .brand-dot { width: 120px; height: 120px; }
  .back-brand .brand-name { font-size: 18px; text-align: center; line-height: 1.25; white-space: normal; }
</style>
</head>
<body>

  <section class="card card--front" aria-label="Front of card">
    <div class="front-brand">
      <span class="brand-dot"></span>
      <span class="brand-name">Public Adjusters Collective, Inc.</span>
    </div>
  </section>

  <section class="card card--back" aria-label="Back of card">
    <svg class="back-art" viewBox="0 0 640 366" aria-hidden="true">
      <polygon points="0,22 38,22 18,58 0,58" fill="var(--orange)"/>
      <polygon points="44,22 56,22 56,58 24,58" fill="var(--navy)"/>
      <polygon points="0,296 300,296 290,314 0,314" fill="var(--orange)"/>
      <polygon points="306,300 640,300 640,366 270,366" fill="var(--navy)"/>
    </svg>

    <div class="person">
      <p class="person-name">Daniel Reyes</p>
      <p class="person-role">Managing Director</p>
    </div>

    <ul class="contact">
      <li class="address">4820 Lakeview Avenue</li>
      <li class="address">Chicago, IL 60614.</li>
      <li>
        <svg viewBox="0 0 10 10"><path d="M2 0.5 L4 2.5 L3 4 Q4.5 6 6 7 L7.5 6 L9.5 8 L8 9.5 Q3 9 0.5 2 Z" fill="var(--orange)"/></svg>
        312-555 0148
      </li>
      <li>
        <svg viewBox="0 0 10 10"><rect x="0.5" y="2" width="9" height="6.5" fill="var(--orange)"/><path d="M0.5 2 L5 5.5 L9.5 2" stroke="#fff" stroke-width="0.9" fill="none"/></svg>
        hello@qpacollective.com
      </li>
      <li>
        <svg viewBox="0 0 10 10"><circle cx="5" cy="5" r="4.5" fill="var(--orange)"/></svg>
        www.qpacollective.com
      </li>
    </ul>

    <div class="back-brand">
      <span class="brand-dot"></span>
      <span class="brand-name">Public Adjusters Collective</span>
    </div>
  </section>

</body>
</html>
```